real esate business card with company logo and name

we need a business card design for a real esate company

The company name is Walsh & Brand Pty Ltd, and we have our logo designed and will upload. We want classic or moden feel. Black or white background. looks more textured. Should include folowinginformations
Owen Walsh and Lucy Brand
Sales Agents & Onsite Manager
p: 07 5948 2063
F: 07 5948 2174
M:0431 857 219
3/42 Marlow Crescent, FERNLEA QLD 4213

We want this business card looks professonal. Thank you in advance.

Industry/Entity Type

Real Estate Agent

Contact Information for Business Card

Owen Walsh and Lucy Brand
Onsite Manager & Sales Agents
p: 07 5948 2063
M:0431 857 219

Font styles to use
Serif

Colors
000000
fbfbfb
333333
959595

Requirements
Must have
• company logo and name, black or white back ground

```html
<!DOCTYPE html>
<html lang="en">
<head>
<meta charset="utf-8">
<title>Walsh &amp; Brand Pty Ltd – Business Card</title>
<link href="https://fonts.googleapis.com/css2?family=Tinos:wght@400;700&display=swap" rel="stylesheet">
<style>
  :root {
    --black: #000000;
    --white: #fbfbfb;
    --charcoal: #333333;
    --grey: #959595;
    --stage: #d6d3ce;
    --rule: #d8d8d8;
    --ghost: #121212;
  }
  * { margin: 0; padding: 0; box-sizing: border-box; }
  html, body {
    width: 1200px; height: 892px; overflow: hidden;
    background: var(--stage);
  }
  .card {
    position: absolute; left: 100px; top: 161px;
    width: 1000px; height: 570px;
    background: var(--black);
    overflow: hidden;
    font-family: "Tinos", "Times New Roman", serif;
    box-shadow: 0 14px 30px rgba(0,0,0,.35);
  }
  .ghost-mark {
    position: absolute; right: 40px; top: 250px;
    width: 240px; height: 240px;
    background: var(--ghost);
  }
  .divider {
    position: absolute; left: 200px; right: 0; top: 318px;
    height: 5px; background: var(--rule);
  }
  .brand {
    position: absolute; left: 60px; top: 140px;
  }
  .brand-square {
    width: 120px; height: 120px;
    background: linear-gradient(135deg, var(--grey), #5e5e5e);
  }
  .brand-name {
    margin-top: 18px;
    font-size: 17px; letter-spacing: 1px; text-transform: uppercase;
    color: var(--charcoal); white-space: nowrap;
  }
  .people {
    position: absolute; right: 60px; top: 30px;
    text-align: right;
  }
  .person-name {
    font-size: 46px; line-height: 1.05; color: var(--white);
  }
  .person-role {
    font-size: 22px; line-height: 1.3; color: var(--grey);
    margin-bottom: 6px;
  }
  .contacts {
    position: absolute; left: 290px; top: 360px;
    list-style: none;
    font-size: 25px; line-height: 30px; color: #b4b4b4;
  }
  .contacts li { display: flex; align-items: center; gap: 16px; }
  .contacts .icon {
    width: 18px; height: 18px; flex: none;
    background: var(--grey); border-radius: 2px;
    display: flex; align-items: center; justify-content: center;
  }
  .contacts .indent { padding-left: 34px; }
</style>
</head>
<body>
  <main class="card">
    <div class="ghost-mark" aria-hidden="true"></div>
    <div class="divider"></div>

    <div class="brand">
      <div class="brand-square" aria-hidden="true"></div>
      <div class="brand-name">Walsh &amp; Brand Pty Ltd.</div>
    </div>

    <div class="people">
      <div class="person-name">Owen Walsh</div>
      <div class="person-role">Onsite Manager</div>
      <div class="person-name">Lucy Brand</div>
      <div class="person-role">Sales Agents</div>
    </div>

    <ul class="contacts">
      <li>
        <span class="icon">
          <svg width="12" height="12" viewBox="0 0 12 12"><path d="M2.5 1l2 2-1 1.5a7 7 0 0 0 4 4L9 7.5l2 2L9.5 11C5 11 1 7 1 2.5z" fill="#000"/></svg>
        </span>07 5948 2063
      </li>
      <li>
        <span class="icon">
          <svg width="12" height="12" viewBox="0 0 12 12"><rect x="3" y="1" width="6" height="10" rx="1" fill="#000"/><rect x="4" y="2.5" width="4" height="5" fill="#959595"/></svg>
        </span>0431 857 219
      </li>
      <li>
        <span class="icon">
          <svg width="12" height="12" viewBox="0 0 12 12"><path d="M6 1a3.5 3.5 0 0 1 3.5 3.5C9.5 7 6 11 6 11S2.5 7 2.5 4.5A3.5 3.5 0 0 1 6 1z" fill="#000"/><circle cx="6" cy="4.5" r="1.3" fill="#959595"/></svg>
        </span>3/42 Marlow Crescent,
      </li>
      <li class="indent">FERNLEA QLD 4213</li>
    </ul>
  </main>
</body>
</html>
```